Tom Parrish Acreage Services LLC

Need a business card design for a new company based in Pine Hollow, MS. We specialize in under-brush clearing, forestry mulching, cutover mulching, right of way clearing, land line & fence row clearing, bush hogging, land clearing, wildlife food plots. We use compact track loaders and tractors. I will attach a picture of a compact track loader I would like to have on the card design if possible.

Target Market(s)

Businesses / Land Owners

Contact Information for Business Card

Tom Parrish
Owner / Operator

Pine Hollow, MS

Call/Text: 601-555-0187
tpacreage@mailbrook.net
FB: @tomparrishacreageservicesllc

Font styles to use
Serif
Sans Serif

Requirements
Must have
• Contact info, city & state. Description of services.
Nice to have
• Not overwhelming back ground but eye and interest catching with clear objection of the business

```html
<!DOCTYPE html>
<html lang="en">
<head>
<meta charset="utf-8">
<title>Tom Parrish Acreage Services LLC — Business Card</title>
<link rel="stylesheet" href="https://fonts.googleapis.com/css2?family=Open+Sans:wght@300;400;600;700;800&display=swap">
<style>
  :root {
    --bg: #2a2a2c;
    --card: #ffffff;
    --ink: #3d3d3f;
    --ink-soft: #555558;
    --gold: #f2c230;
    --gold-deep: #e0ad1a;
    --photo-dark: #5b4a1e;
    --photo-mid: #a8922f;
    --photo-light: #d9cf86;
  }
  * { box-sizing: border-box; margin: 0; padding: 0; }
  html, body { width: 1200px; height: 900px; overflow: hidden; }
  body {
    background: var(--bg);
    font-family: "Open Sans", Arial, sans-serif;
    display: flex;
    flex-direction: column;
    align-items: center;
    justify-content: center;
    gap: 40px;
  }
  .card {
    width: 700px;
    height: 400px;
    background: var(--card);
    position: relative;
    overflow: hidden;
    box-shadow: 0 10px 30px rgba(0,0,0,.45);
  }

  /* Front */
  .card-front {
    display: flex;
    flex-direction: column;
    align-items: center;
    justify-content: center;
    text-align: center;
    color: var(--ink);
  }
  .company-name { font-weight: 800; font-size: 46px; line-height: 1; letter-spacing: -0.5px; }
  .company-suffix { font-weight: 300; font-size: 30px; line-height: 1.15; }
  .company-city { color: var(--gold); font-weight: 600; font-size: 22px; margin-top: 2px; }
  .owner-name { margin-top: 22px; font-weight: 800; font-size: 30px; letter-spacing: 1px; line-height: 1; }
  .owner-role { color: var(--gold); font-weight: 600; font-size: 18px; margin-top: 2px; }
  .contact-icons { display: flex; gap: 12px; margin: 14px 0 10px; }
  .contact-icons svg { width: 26px; height: 26px; display: block; }
  .contact-list { list-style: none; font-size: 16px; line-height: 1.5; color: var(--ink-soft); }

  /* Back */
  .card-back { display: flex; }
  .machine-photo {
    position: absolute;
    inset: 0;
    background:
      linear-gradient(100deg, var(--photo-dark) 0%, var(--photo-mid) 30%, var(--photo-light) 48%, rgba(255,255,255,0) 66%),
      var(--card);
  }
  .services {
    position: relative;
    margin-left: auto;
    margin-right: 40px;
    align-self: center;
    width: 360px;
  }
  .services-title { font-weight: 800; font-size: 30px; color: var(--ink); letter-spacing: .5px; margin-bottom: 8px; }
  .services-list { list-style: none; }
  .services-list li {
    font-weight: 800;
    font-size: 16px;
    color: var(--gold-deep);
    text-transform: uppercase;
    line-height: 1.55;
    position: relative;
    padding-left: 18px;
  }
  .services-list li::before {
    content: "";
    position: absolute;
    left: 0; top: 9px;
    width: 7px; height: 7px;
    background: var(--ink);
  }
</style>
</head>
<body>
  <section class="card card-front">
    <h1 class="company-name">Tom Parrish</h1>
    <p class="company-suffix">Acreage Services LLC</p>
    <p class="company-city">Pine Hollow, MS</p>
    <h2 class="owner-name">TOM PARRISH</h2>
    <p class="owner-role">Owner / Operator</p>
    <div class="contact-icons">
      <svg viewBox="0 0 26 26" aria-label="Phone">
        <circle cx="13" cy="13" r="13" fill="var(--gold)"/>
        <path d="M9 7.5c.6-.4 1.3-.3 1.6.3l1.2 2.2c.3.5.1 1.1-.3 1.4l-.8.6c.6 1.6 1.8 2.8 3.4 3.4l.6-.8c.3-.4.9-.6 1.4-.3l2.2 1.2c.6.3.7 1 .3 1.6l-.8 1c-.5.6-1.3.8-2 .6-3.6-1.1-6.4-3.9-7.5-7.5-.2-.7 0-1.5.6-2z" fill="#fff"/>
      </svg>
      <svg viewBox="0 0 26 26" aria-label="Email">
        <circle cx="13" cy="13" r="13" fill="var(--gold)"/>
        <rect x="7" y="9" width="12" height="8.5" rx="1" fill="none" stroke="#fff" stroke-width="1.6"/>
        <path d="M7.5 9.8 13 14l5.5-4.2" fill="none" stroke="#fff" stroke-width="1.6"/>
      </svg>
      <svg viewBox="0 0 26 26" aria-label="Social page">
        <circle cx="13" cy="13" r="13" fill="var(--gold)"/>
      </svg>
    </div>
    <ul class="contact-list">
      <li>601-555-0187</li>
      <li>tpacreage@mailbrook.net</li>
      <li>@tomparrishacreageservicesllc</li>
    </ul>
  </section>

  <section class="card card-back">
    <div class="machine-photo" role="img" aria-label="Photo of a yellow compact track loader with a mulching head in a sunlit pine forest, fading to white"></div>
    <div class="services">
      <h3 class="services-title">WE SPECIALIZE IN</h3>
      <ul class="services-list">
        <li>Under-brush clearing</li>
        <li>Forestry mulching</li>
        <li>Right of way clearing</li>
        <li>Land line &amp; fence row clearing</li>
        <li>Bush hogging</li>
        <li>Land clearing</li>
        <li>Wildlife food plots</li>
      </ul>
    </div>
  </section>
</body>
</html>
```